Music Quizz Application

Hello,

I want a new design for my Blind test (music quizz) application on Korvex. You will find attached the images I want to replace. I need something with the same element (menu / song title) but with a different look!

Same, new icon, you have carte blanche to this one.

I am looking for something fresh…. I'm looking for something with a real artistic choice, contrast, colours, etc.

As a marketing screenshot, I want something classic, you'll find an example attached, feel free to innovate.

To sum-up :

- One new view for my App
- One new icon
- One marketing screenshot

screen resolution :
640×960
icon resolution :
1024x1024

Target Market(s)

15-30 years

Industry/Entity Type

Marketing

```html
<!DOCTYPE html>
<html lang="en">
<head>
<meta charset="utf-8">
<title>Earshot – Score rules</title>
<link rel="stylesheet" href="https://fonts.googleapis.com/css2?family=Ubuntu:wght@300;400;500&family=Arimo:wght@700&display=swap">
<style>
  :root {
    --bar-bg: #000000;
    --bar-text: #e9e9e9;
    --brand-ink: #221f1c;
    --panel-top: #3f3d3b;
    --panel-bottom: #0f0d0c;
    --panel-edge: #1a1a1a;
    --panel-rule: #6a6866;
    --panel-text: #ffffff;
  }
  * { box-sizing: border-box; margin: 0; padding: 0; }
  html, body { width: 800px; height: 1200px; overflow: hidden; background: var(--bar-bg); }
  .screen { position: relative; width: 800px; height: 1200px; overflow: hidden; font-family: "Ubuntu", sans-serif; }

  .backdrop {
    position: absolute; inset: 50px 0 0 0;
    background:
      radial-gradient(ellipse 260px 320px at 40px 330px, rgba(30,170,120,0.85), transparent 70%),
      radial-gradient(ellipse 200px 260px at 60px 800px, rgba(60,190,150,0.55), transparent 70%),
      radial-gradient(ellipse 260px 240px at 700px 120px, rgba(200,60,20,0.85), transparent 70%),
      radial-gradient(ellipse 300px 340px at 720px 420px, rgba(245,180,40,0.95), transparent 70%),
      radial-gradient(ellipse 280px 260px at 230px 80px, rgba(20,40,20,0.9), transparent 70%),
      radial-gradient(ellipse 360px 300px at 400px 620px, rgba(255,255,250,0.95), transparent 75%),
      radial-gradient(ellipse 300px 240px at 650px 1150px, rgba(150,40,10,0.9), transparent 70%),
      radial-gradient(ellipse 260px 260px at 80px 1150px, rgba(10,10,10,0.9), transparent 70%),
      linear-gradient(180deg, #4a6a3a 0%, #e8e2c8 45%, #8a6a40 80%, #2a1a10 100%);
  }

  .status-bar {
    position: absolute; top: 0; left: 0; width: 800px; height: 50px;
    background: var(--bar-bg); color: var(--bar-text);
    font-family: "Arimo", sans-serif; font-weight: 700; font-size: 28px;
    display: flex; align-items: center; padding: 0 12px;
  }
  .status-carrier { display: flex; align-items: center; gap: 10px; }
  .status-net { margin-left: 16px; font-size: 26px; }
  .status-time { position: absolute; left: 0; right: 0; text-align: center; font-size: 30px; pointer-events: none; }
  .status-right { margin-left: auto; display: flex; align-items: center; gap: 14px; }

  .brand {
    position: absolute; top: 430px; left: 0; width: 800px; text-align: center;
    font-family: "Ubuntu", sans-serif; font-weight: 300; font-size: 96px;
    color: var(--brand-ink); letter-spacing: -1px;
  }

  .score-panel {
    position: absolute; left: 109px; top: 610px; width: 585px; height: 465px;
    background: linear-gradient(180deg, var(--panel-top) 0%, #2a2827 40%, var(--panel-bottom) 100%);
    border: 2px solid var(--panel-edge); border-radius: 4px;
    color: var(--panel-text);
    box-shadow: 0 2px 8px rgba(0,0,0,0.35);
  }
  .score-panel__title {
    height: 87px; display: flex; align-items: center; justify-content: center;
    font-weight: 500; font-size: 30px; padding-left: 30px;
    border-bottom: 2px solid var(--panel-rule);
  }
  .score-panel__body { padding: 22px 26px; font-size: 26px; line-height: 35px; font-weight: 400; }
  .score-panel__body p { margin-bottom: 35px; }
</style>
</head>
<body>
<main class="screen">
  <div class="backdrop" role="img" aria-label="Soft blurred background of green, yellow, orange and white colour glows"></div>

  <header class="status-bar">
    <div class="status-carrier">
      <svg width="44" height="14" viewBox="0 0 44 14" aria-hidden="true">
        <rect x="0" y="4" width="7" height="8" fill="#e9e9e9"/>
        <rect x="10" y="10" width="5" height="2" fill="#e9e9e9"/>
        <rect x="18" y="10" width="5" height="2" fill="#e9e9e9"/>
        <rect x="26" y="10" width="5" height="2" fill="#e9e9e9"/>
        <rect x="34" y="10" width="5" height="2" fill="#e9e9e9"/>
      </svg>
      <span>Lumio</span>
    </div>
    <span class="status-net">3G</span>
    <span class="status-time">12:14</span>
    <div class="status-right">
      <svg width="18" height="30" viewBox="0 0 18 30" aria-hidden="true">
        <path d="M2 8 L15 21 L9 27 L9 3 L15 9 L2 22" fill="none" stroke="#8a8a8a" stroke-width="2.5"/>
      </svg>
      <span>89 %</span>
      <svg width="44" height="24" viewBox="0 0 44 24" aria-hidden="true">
        <rect x="1.5" y="2.5" width="36" height="19" rx="2" fill="none" stroke="#e9e9e9" stroke-width="2.5"/>
        <rect x="38" y="8" width="4" height="8" fill="#e9e9e9"/>
        <rect x="4" y="5" width="28" height="14" fill="#e9e9e9"/>
        <path d="M20 6 L14 13 L19 13 L17 19 L24 11 L19 11 Z" fill="#000"/>
      </svg>
    </div>
  </header>

  <h1 class="brand">Earshot</h1>

  <section class="score-panel">
    <h2 class="score-panel__title">How the score is calculated?</h2>
    <div class="score-panel__body">
      <p>Points are awarded as follows:</p>
      <p>-1 for each incorrect answer</p>
      <p>+5 or +10 for each correct answer (depending upon whether your game features a5 or 10 possible answers)</p>
      <p>1 point deducted for every 10 seconds that pass.</p>
    </div>
  </section>
</main>
</body>
</html>
```